cryotherapy business . Whole Body Cryotherapy, Localised Cryotherapy, Cryofacials

Need home page plus services, about, pricing, online booking, contact and blog page

I want something slick, hip and professional. Our studio colours are duck egg blue, white and grey

I would also like a social media scroll at the bottom of every page

I will upload some web designs that I like the look of

Target Market(s)

Men and Women 25-45

Industry/Entity Type

Health And Wellness

Coding

Coded - Design and coding required

Number of Pages Required

5+ page

Font styles to use
Serif
Sans Serif

Requirements
Must have
• Must be eye catching and easy to navigate
Nice to have
• animation
Should not have
• Not sure what the site should not have. I am fairly open to ideas as this is a brand new business.

```html
<!DOCTYPE html>
<html lang="en">
<head>
<meta charset="utf-8">
<title>Frostline Studio – Home Page Concepts</title>
<link href="https://fonts.googleapis.com/css2?family=Open+Sans:wght@300;400;600;700&display=swap" rel="stylesheet">
<style>
:root{
  --duck-egg:#cfe9df;
  --mint-btn:#c6e6d9;
  --ink:#1f2326;
  --text:#4a4f55;
  --muted:#6f757b;
  --line:#dcdfe2;
  --band:#f6f6f6;
  --slate:#6c6f74;
  --footer:#2e2f31;
  --white:#ffffff;
}
*{box-sizing:border-box;margin:0;padding:0}
html,body{width:727px;height:1200px;overflow:hidden;background:var(--white)}
body{font-family:'Open Sans',sans-serif;color:var(--ink);position:relative}
.concept{position:absolute;width:720px;height:2435px;transform-origin:0 0;transform:scale(.4856);background:var(--white)}
.concept--a{left:10px;top:6px}
.concept--b{left:368px;top:7px}

.topbar{height:30px;display:flex;align-items:center;padding:0 70px;font-size:11px;font-weight:600;gap:14px}
.concept--a .topbar{background:var(--duck-egg)}
.topbar .social{margin-left:auto;display:flex;gap:8px}
.dot{width:16px;height:16px;border-radius:50%;background:var(--white);border:1px solid var(--line)}
.ico{width:10px;height:10px;vertical-align:-1px;margin-right:3px}

.hero{position:relative;height:362px;overflow:hidden}
.hero-photo{position:absolute;inset:0}
.concept--a .hero-photo{background:linear-gradient(120deg,#d9dde4 0%,#9fa9b9 45%,#7d8aa0 70%,#c7ccd6 100%)}
.concept--b .hero-photo{background:radial-gradient(ellipse at 50% 75%,#e8edf5 0%,#9db2d6 35%,#3f69c9 70%,#2f5cc4 100%)}
.nav{position:absolute;top:0;left:0;right:0;height:38px;display:flex;align-items:center;padding:0 67px;background:linear-gradient(rgba(40,50,70,.35),rgba(40,50,70,0))}
.brand{font-weight:300;font-size:21px;letter-spacing:3px;color:var(--white);margin-right:22px}
.nav ul{display:flex;gap:12px;list-style:none;font-size:10px;font-weight:600;color:var(--white)}
.nav li::after{content:" ▾";font-size:8px}
.hero-title{position:absolute;left:0;right:0;text-align:center;color:var(--white);font-size:31px;font-weight:600;letter-spacing:.5px;text-shadow:0 1px 4px rgba(0,0,0,.25)}
.concept--a .hero-title{top:158px}
.concept--b .hero-title{top:208px}
.btn{display:inline-block;background:var(--mint-btn);color:var(--ink);font-size:10px;font-weight:700;padding:7px 11px;letter-spacing:.3px}
.hero .btn{position:absolute;left:50%;transform:translateX(-50%)}
.concept--a .hero .btn{top:214px}
.concept--b .hero .btn{top:264px}
.arrow-circle{position:absolute;top:170px;width:24px;height:24px;border:1px solid var(--white);border-radius:50%}
.concept--b .arrow-circle{top:171px}
.arrow-circle svg{width:22px;height:22px}
.arrow-circle.left{left:28px}.arrow-circle.right{right:30px}

.section-title{text-align:center;font-size:22px;font-weight:600;letter-spacing:.3px}
.services{padding-top:48px;height:424px}
.service-row{display:flex;gap:13px;margin:12px 67px 0}
.service-card{width:187px;height:285px;border:1px solid var(--line);display:flex;flex-direction:column}
.service-card .copy{height:145px;text-align:center;padding:10px 8px 0}
.service-card h3{font-size:11px;font-weight:400;letter-spacing:.3px}
.service-card .tag{font-size:8px;font-weight:600;margin:4px 0 6px}
.service-card p{font-size:8px;line-height:16px;color:var(--text)}
.service-card .btn{margin-top:8px;font-size:9px;padding:5px 10px}
.service-card .photo{height:140px}
.service-card--raised{box-shadow:0 2px 6px rgba(0,0,0,.15)}
.photo--cabin{background:linear-gradient(135deg,#4b3fa8,#2a2f6e 60%,#6c6fb0)}
.photo--wand{background:linear-gradient(135deg,#2d4d73,#9fb3c5 60%,#5e7187)}
.photo--facial{background:linear-gradient(135deg,#c9d3c8,#e6dcd8 55%,#a7a39d)}

.pricing{background:var(--band);height:327px;padding-top:42px;margin-top:-16px}
.price-row{display:flex;gap:12px;margin:22px 67px 0}
.price-card{width:138px;height:194px;border:1px solid var(--line);background:var(--white);text-align:center}
.price-head{background:var(--duck-egg);height:82px;padding-top:8px}
.price-head .plan{font-size:10px}
.price-head .amount{font-size:33px;font-weight:600;line-height:36px}
.price-head .amount small{font-size:10px;vertical-align:-2px}
.price-head .note{font-size:7px;color:var(--text)}
.price-card ul{list-style:none;font-size:8px;color:var(--text);text-align:left;padding:12px 0 0 20px;line-height:16px}
.price-card li::before{content:"✓ ";color:#7cc4a8;font-weight:700}
.price-card .btn{margin-top:8px;font-size:9px;padding:5px 9px}

.about{padding-top:44px;height:288px}
.about-row{display:flex;gap:25px;margin:16px 67px 0}
.about-photo{width:183px;height:155px;background:linear-gradient(160deg,#e4e8ea,#c9cfd3 55%,#f1f1f1)}
.about-copy{flex:1;font-size:8px;line-height:17px;color:var(--text);text-align:justify}
.about-copy .btn{margin-top:14px;font-size:9px}

.booking{height:180px;background:linear-gradient(135deg,#74777c,#5f6267 60%,#6d7075);text-align:center;color:var(--white);padding-top:28px}
.booking h2{font-size:22px;font-weight:600}
.booking p{font-size:15px;margin:12px 0 16px;font-weight:400}
.booking .btn{font-size:9px;padding:7px 18px}

.press{padding-top:50px;height:334px;position:relative}
.press-row{position:relative;margin:14px 67px 0;height:190px;display:flex;gap:11px;align-items:flex-start}
.press-item{position:relative}
.press-item .frame{height:140px}
.press-item--wide{width:282px}
.press-item--small{width:141px;margin-top:25px}
.press-item--small .frame{height:85px}
.concept--b .press-row{gap:22px}
.frame--booth{background:linear-gradient(100deg,#8fb6de,#4d86c9 40%,#b4c9e0 70%,#e7eef4)}
.frame--mask{background:linear-gradient(110deg,#e8dede,#f6f3f2 50%,#cfc6c6)}
.frame--lie{background:linear-gradient(110deg,#1d3f7e,#cdd7e6 60%,#f3f3f3)}
.frame--mist{background:linear-gradient(120deg,#a9a5bb,#d8d5e2 50%,#ecebf1)}
.play{position:absolute;left:50%;top:70px;transform:translate(-50%,-50%);width:30px;height:30px}
.press-item h4{font-size:11px;font-weight:400;margin-top:6px;letter-spacing:.2px}
.press-item p{font-size:8px;color:var(--text);line-height:17px}
.side-arrow{position:absolute;top:58px;width:14px;height:22px}
.side-arrow.left{left:-28px}.side-arrow.right{right:-28px}

.locations{padding-top:0;height:340px}
.locations .section-title{font-weight:700}
.loc-row{display:flex;gap:50px;margin:24px 67px 0}
.loc-card{width:268px;border:1px solid var(--line)}
.map{height:190px}
.map--street{background:linear-gradient(160deg,#eef1f4 0%,#e2e8ee 55%,#d3e0ee 100%)}
.map--aerial{background:linear-gradient(135deg,#5b5d5a,#7a7c74 40%,#4e524d 70%,#6f706a)}
.loc-info{height:60px;display:flex;align-items:center;padding:0 20px;font-size:12px;line-height:17px;justify-content:space-between}
.loc-info svg{width:10px;height:14px}

.footer{height:162px;background:var(--footer);color:var(--white);position:relative;font-size:8px;text-align:center}
.f-col{position:absolute;top:38px;line-height:17px;white-space:nowrap}
.f-col h5{font-size:9px;font-weight:600;margin-bottom:8px}
.f-hours{left:60px;width:150px}
.f-contact{right:40px;width:160px}
.f-brand{position:absolute;left:0;right:0;top:36px;text-align:center}
.f-brand .name{font-size:30px;font-weight:300;letter-spacing:4px}
.f-social{display:flex;justify-content:center;gap:7px;margin-top:8px}
.f-social span{width:24px;height:24px;border-radius:50%;border:1px solid var(--white)}
.copyright{position:absolute;bottom:12px;left:0;right:0;font-size:9px}
</style>
</head>
<body>

<main class="concept concept--a">
  <div class="topbar">
    <span><svg class="ico" viewBox="0 0 10 10"><path d="M2 1l2 2-1 1.3c.6 1.2 1.5 2.1 2.7 2.7L7 6l2 2-1.2 1.5C4.5 9.3.7 5.5 1 2.2z" fill="#1f2326"/></svg>555-014-2290</span>
    <span><svg class="ico" viewBox="0 0 10 10"><rect x="1" y="2" width="8" height="6" fill="#1f2326"/></svg>hello@frostline-studio.com</span>
    <span class="social"><span class="dot"></span><span class="dot"></span><span class="dot"></span></span>
  </div>
  <section class="hero">
    <div class="hero-photo" role="img" aria-label="Therapist opening a whole body cryotherapy chamber with mist at its base"></div>
    <nav class="nav"><span class="brand">FROSTLINE</span>
      <ul><li>HOME</li><li>SERVICES</li><li>ABOUT</li><li>PRICING</li><li>ONLINE BOOKING</li><li>CONTACT &amp; BLOG</li></ul></nav>
    <h1 class="hero-title">REDUCE PAIN &amp; INFLAMMATION</h1>
    <span class="btn">MAKE APPOINTMENT</span>
    <span class="arrow-circle left"><svg viewBox="0 0 22 22"><path d="M13 7l-4 4 4 4" stroke="#fff" stroke-width="1.6" fill="none"/></svg></span>
    <span class="arrow-circle right"><svg viewBox="0 0 22 22"><path d="M9 7l4 4-4 4" stroke="#fff" stroke-width="1.6" fill="none"/></svg></span>
  </section>

  <section class="services">
    <h2 class="section-title">SERVICES</h2>
    <div class="service-row">
      <article class="service-card">
        <div class="copy"><h3>WHOLE BODY CRYOTHERAPY</h3><div class="tag">Relief &amp; rejuvenation for your entire body</div>
          <p>hole Body Cryotherapy is a quick, non-invasive process that exposes your body to extreme cold up to -250F.</p><span class="btn">KNOW MORE</span></div>
        <div class="photo photo--cabin" role="img" aria-label="Client standing in a violet-lit cryotherapy cabin"></div>
      </article>
      <article class="service-card service-card--raised">
        <div class="photo photo--wand" role="img" aria-label="Therapist holding a localised cryotherapy wand"></div>
        <div class="copy"><h3>LOCALISED CRYOTHERAPY</h3><div class="tag">Reduce pain, inflammation &amp; swelling<br>in targeted areas</div>
          <p>Local cryotherapy acts as a higher intensity, more efficient form of "icing." With the use of liquid nitrogen,</p><span class="btn">KNOW MORE</span></div>
      </article>
      <article class="service-card">
        <div class="copy"><h3>CRYOFACIALS</h3><div class="tag">Slow down the aging process</div>
          <p>Cryo Facials apply pressurized liquid nitrogen vapors to the face, neck and scalp to help stimulate and improve</p><span class="btn">KNOW MORE</span></div>
        <div class="photo photo--facial" role="img" aria-label="Client receiving a cryofacial treatment"></div>
      </article>
    </div>
  </section>

  <section class="pricing">
    <h2 class="section-title">PRICING</h2>
    <div class="price-row">
      <div class="price-card"><div class="price-head"><div class="plan">SINGLE</div><div class="amount"><small>$</small>40</div><div class="note">LOREM IPSUM IS SIMPLY</div></div><ul><li>Lorem Ipsum is simply</li><li>Lorem Ipsum is simply</li><li>Lorem Ipsum is simply</li></ul><span class="btn">BUY NOW</span></div>
      <div class="price-card"><div class="price-head"><div class="plan">10 PACK</div><div class="amount"><small>$</small>380</div><div class="note">LOREM IPSUM IS SIMPLY</div></div><ul><li>Lorem Ipsum is simply</li><li>Lorem Ipsum is simply</li><li>Lorem Ipsum is simply</li></ul><span class="btn">BUY NOW</span></div>
      <div class="price-card"><div class="price-head"><div class="plan">20 PACK</div><div class="amount"><small>$</small>720</div><div class="note">LOREM IPSUM IS SIMPLY</div></div><ul><li>Lorem Ipsum is simply</li><li>Lorem Ipsum is simply</li><li>Lorem Ipsum is simply</li></ul><span class="btn">BUY NOW</span></div>
      <div class="price-card"><div class="price-head"><div class="plan">MONTHLY*</div><div class="amount"><small>$</small>400</div><div class="note">LOREM IPSUM IS SIMPLY</div></div><ul><li>Lorem Ipsum is simply</li><li>Lorem Ipsum is simply</li><li>Lorem Ipsum is simply</li></ul><span class="btn">BUY NOW</span></div>
    </div>
  </section>

  <section class="about">
    <h2 class="section-title">ABOUT US</h2>
    <div class="about-row">
      <div class="about-photo" role="img" aria-label="Client relaxing under cryo mist during a facial treatment"></div>
      <div class="about-copy">Originally invented by doctors as a powerful anti-inflammatory tool, cryotherapy is a quick, noninvasive process that exposes your body to extreme cold of up to -250°F. This sudden drop in temperature increases circulation and pumps reoxygenated and nutrient enriched blood back into the bloodstream reducing pain &amp; inflammation and alleviating sore muscles. It's also known to release 'feel good' endorphins that help improve sleep, reduce stress, and increase your metabolism.<br><span class="btn">KNOW MORE</span></div>
    </div>
  </section>

  <section class="booking" role="img" aria-label="Grey architectural backdrop">
    <h2>ONLINE BOOKING</h2><p>Choose The Right Procedure For You</p><span class="btn">BOOKING NOW</span>
  </section>

  <section class="press">
    <h2 class="section-title">PRESS</h2>
    <div class="press-row">
      <svg class="side-arrow left" viewBox="0 0 14 22"><path d="M11 2L3 11l8 9" stroke="#555" stroke-width="2.5" fill="none"/></svg>
      <div class="press-item press-item--wide"><div class="frame frame--booth" role="img" aria-label="Video still of a client in a blue-lit cryo chamber"></div>
        <svg class="play" viewBox="0 0 30 30"><circle cx="15" cy="15" r="13" stroke="#fff" stroke-width="2" fill="none"/><path d="M12 9l9 6-9 6z" fill="#fff"/></svg>
        <h4>WHOLE BODY CRYOTHERAPY</h4><p>Lorem ipsum dolor sit amet, consectetur adipiscing elit,<br>sed do eiusmod tempor incididunt</p></div>
      <div class="press-item press-item--small"><div class="frame frame--mask" role="img" aria-label="Video still of a facial treatment"></div></div>
      <div class="press-item press-item--small"><div class="frame frame--lie" role="img" aria-label="Video still of a client lying in a treatment room"></div></div>
      <svg class="side-arrow right" viewBox="0 0 14 22"><path d="M3 2l8 9-8 9" stroke="#555" stroke-width="2.5" fill="none"/></svg>
    </div>
  </section>

  <section class="locations">
    <h2 class="section-title">OUR LOCATIONS</h2>
    <div class="loc-row">
      <div class="loc-card"><div class="map map--street" role="img" aria-label="Street map of the Northbay studio"></div>
        <div class="loc-info"><span>NORTHBAY<br>12 HARBOR LANE 2ND FLOOR</span><svg viewBox="0 0 10 14"><path d="M2 2l5 5-5 5" stroke="#1f2326" stroke-width="2" fill="none"/></svg></div></div>
      <div class="loc-card"><div class="map map--aerial" role="img" aria-label="Aerial map of the Eastfield studio"></div>
        <div class="loc-info"><span>EASTFIELD<br>400 MILL ROAD 3RD FLOOR</span><svg viewBox="0 0 10 14"><path d="M2 2l5 5-5 5" stroke="#1f2326" stroke-width="2" fill="none"/></svg></div></div>
    </div>
  </section>

  <footer class="footer">
    <div class="f-col f-hours"><h5>HOURS</h5>MONDAY - FRIDAY 6:00 AM - 7:00 PM<br>SATURDAY CLOSED<br>SUNDAY CLOSED</div>
    <div class="f-brand"><div class="name">FROSTLINE</div><div class="f-social"><span></span><span></span><span></span><span></span></div></div>
    <div class="f-col f-contact"><h5>CONTACT US</h5>555-014-2290<br>HELLO@FROSTLINE-STUDIO.COM</div>
    <div class="copyright">© Copyright 2019 . All Rights Reserved. Terms and Conditions | Privacy Policy</div>
  </footer>
</main>

<main class="concept concept--b">
  <div class="topbar">
    <span><svg class="ico" viewBox="0 0 10 10"><path d="M2 1l2 2-1 1.3c.6 1.2 1.5 2.1 2.7 2.7L7 6l2 2-1.2 1.5C4.5 9.3.7 5.5 1 2.2z" fill="#1f2326"/></svg>555-014-2290</span>
    <span><svg class="ico" viewBox="0 0 10 10"><rect x="1" y="2" width="8" height="6" fill="#1f2326"/></svg>hello@frostline-studio.com</span>
    <span class="social"><span class="dot"></span><span class="dot"></span><span class="dot"></span></span>
  </div>
  <section class="hero">
    <div class="hero-photo" role="img" aria-label="Client inside a blue cryo chamber surrounded by rising mist"></div>
    <nav class="nav"><span class="brand">FROSTLINE</span>
      <ul><li>HOME</li><li>SERVICES</li><li>ABOUT</li><li>PRICING</li><li>ONLINE BOOKING</li><li>CONTACT &amp; BLOG</li></ul></nav>
    <h1 class="hero-title">REDUCE PAIN &amp; INFLAMMATION</h1>
    <span class="btn">MAKE APPOINTMENT</span>
    <span class="arrow-circle left"><svg viewBox="0 0 22 22"><path d="M13 7l-4 4 4 4" stroke="#fff" stroke-width="1.6" fill="none"/></svg></span>
    <span class="arrow-circle right"><svg viewBox="0 0 22 22"><path d="M9 7l4 4-4 4" stroke="#fff" stroke-width="1.6" fill="none"/></svg></span>
  </section>

  <section class="services">
    <h2 class="section-title">SERVICES</h2>
    <div class="service-row">
      <article class="service-card">
        <div class="copy"><h3>WHOLE BODY CRYOTHERAPY</h3><div class="tag">Relief &amp; rejuvenation for your entire body</div>
          <p>hole Body Cryotherapy is a quick, non-invasive process that exposes your body to extreme cold up to -250F.</p><span class="btn">KNOW MORE</span></div>
        <div class="photo photo--cabin" role="img" aria-label="Client standing in a violet-lit cryotherapy cabin"></div>
      </article>
      <article class="service-card service-card--raised">
        <div class="photo photo--wand" role="img" aria-label="Therapist holding a localised cryotherapy wand"></div>
        <div class="copy"><h3>LOCALISED CRYOTHERAPY</h3><div class="tag">Reduce pain, inflammation &amp; swelling<br>in targeted areas</div>
          <p>Local cryotherapy acts as a higher intensity, more efficient form of "icing." With the use of liquid nitrogen,</p><span class="btn">KNOW MORE</span></div>
      </article>
      <article class="service-card">
        <div class="copy"><h3>CRYOFACIALS</h3><div class="tag">Slow down the aging process</div>
          <p>Cryo Facials apply pressurized liquid nitrogen vapors to the face, neck and scalp to help stimulate and improve</p><span class="btn">KNOW MORE</span></div>
        <div class="photo photo--facial" role="img" aria-label="Client receiving a cryofacial treatment"></div>
      </article>
    </div>
  </section>

  <section class="pricing">
    <h2 class="section-title">PRICING</h2>
    <div class="price-row">
      <div class="price-card"><div class="price-head"><div class="plan">SINGLE</div><div class="amount"><small>$</small>40</div><div class="note">LOREM IPSUM IS SIMPLY</div></div><ul><li>Lorem Ipsum is simply</li><li>Lorem Ipsum is simply</li><li>Lorem Ipsum is simply</li></ul><span class="btn">BUY NOW</span></div>
      <div class="price-card"><div class="price-head"><div class="plan">10 PACK</div><div class="amount"><small>$</small>380</div><div class="note">LOREM IPSUM IS SIMPLY</div></div><ul><li>Lorem Ipsum is simply</li><li>Lorem Ipsum is simply</li><li>Lorem Ipsum is simply</li></ul><span class="btn">BUY NOW</span></div>
      <div class="price-card"><div class="price-head"><div class="plan">20 PACK</div><div class="amount"><small>$</small>720</div><div class="note">LOREM IPSUM IS SIMPLY</div></div><ul><li>Lorem Ipsum is simply</li><li>Lorem Ipsum is simply</li><li>Lorem Ipsum is simply</li></ul><span class="btn">BUY NOW</span></div>
      <div class="price-card"><div class="price-head"><div class="plan">MONTHLY*</div><div class="amount"><small>$</small>400</div><div class="note">LOREM IPSUM IS SIMPLY</div></div><ul><li>Lorem Ipsum is simply</li><li>Lorem Ipsum is simply</li><li>Lorem Ipsum is simply</li></ul><span class="btn">BUY NOW</span></div>
    </div>
  </section>

  <section class="about">
    <h2 class="section-title">ABOUT US</h2>
    <div class="about-row">
      <div class="about-photo" role="img" aria-label="Client relaxing under cryo mist during a facial treatment"></div>
      <div class="about-copy">Originally invented by doctors as a powerful anti-inflammatory tool, cryotherapy is a quick, noninvasive process that exposes your body to extreme cold of up to -250°F. This sudden drop in temperature increases circulation and pumps reoxygenated and nutrient enriched blood back into the bloodstream reducing pain &amp; inflammation and alleviating sore muscles. It's also known to release 'feel good' endorphins that help improve sleep, reduce stress, and increase your metabolism.<br><span class="btn">KNOW MORE</span></div>
    </div>
  </section>

  <section class="booking" role="img" aria-label="Grey architectural backdrop">
    <h2>ONLINE BOOKING</h2><p>Choose The Right Procedure For You</p><span class="btn">BOOKING NOW</span>
  </section>

  <section class="press">
    <h2 class="section-title">PRESS</h2>
    <div class="press-row">
      <svg class="side-arrow left" viewBox="0 0 14 22"><path d="M11 2L3 11l8 9" stroke="#555" stroke-width="2.5" fill="none"/></svg>
      <div class="press-item press-item--wide"><div class="frame frame--booth" role="img" aria-label="Video still of a client in a blue-lit cryo chamber"></div>
        <svg class="play" viewBox="0 0 30 30"><circle cx="15" cy="15" r="13" stroke="#fff" stroke-width="2" fill="none"/><path d="M12 9l9 6-9 6z" fill="#fff"/></svg>
        <h4>WHOLE BODY CRYOTHERAPY</h4><p>Lorem ipsum dolor sit amet, consectetur adipiscing elit,<br>sed do eiusmod tempor incididunt</p></div>
      <div class="press-item press-item--wide"><div class="frame frame--mist" role="img" aria-label="Video still of a client lying under cryo mist"></div>
        <svg class="play" viewBox="0 0 30 30"><circle cx="15" cy="15" r="13" stroke="#fff" stroke-width="2" fill="none"/><path d="M12 9l9 6-9 6z" fill="#fff"/></svg>
        <h4>LOCALISED CRYOTHERAPY</h4><p>Lorem ipsum dolor sit amet, consectetur adipiscing elit,<br>sed do eiusmod tempor incididunt</p></div>
      <svg class="side-arrow right" viewBox="0 0 14 22"><path d="M3 2l8 9-8 9" stroke="#555" stroke-width="2.5" fill="none"/></svg>
    </div>
  </section>

  <section class="locations">
    <h2 class="section-title">OUR LOCATIONS</h2>
    <div class="loc-row">
      <div class="loc-card"><div class="map map--street" role="img" aria-label="Street map of the Northbay studio"></div>
        <div class="loc-info"><span>NORTHBAY<br>12 HARBOR LANE 2ND FLOOR</span><svg viewBox="0 0 10 14"><path d="M2 2l5 5-5 5" stroke="#1f2326" stroke-width="2" fill="none"/></svg></div></div>
      <div class="loc-card"><div class="map map--aerial" role="img" aria-label="Aerial map of the Eastfield studio"></div>
        <div class="loc-info"><span>EASTFIELD<br>400 MILL ROAD 3RD FLOOR</span><svg viewBox="0 0 10 14"><path d="M2 2l5 5-5 5" stroke="#1f2326" stroke-width="2" fill="none"/></svg></div></div>
    </div>
  </section>

  <footer class="footer">
    <div class="f-col f-hours"><h5>HOURS</h5>MONDAY - FRIDAY 6:00 AM - 7:00 PM<br>SATURDAY CLOSED<br>SUNDAY CLOSED</div>
    <div class="f-brand"><div class="name">FROSTLINE</div><div class="f-social"><span></span><span></span><span></span><span></span></div></div>
    <div class="f-col f-contact"><h5>CONTACT US</h5>555-014-2290<br>HELLO@FROSTLINE-STUDIO.COM</div>
    <div class="copyright">© Copyright 2019 . All Rights Reserved. Terms and Conditions | Privacy Policy</div>
  </footer>
</main>

</body>
</html>
```